Business Card Design

We need the business card for our new business based in St. Marys, we manufacture mainly bubble wraps. And we would like the design to use our company logo and also make it easy for people to understand right away we are bubble wrap manufacturer

Industry/Entity Type

Business

Contact Information for Business Card

Cushtane Pty Ltd, 14 Larkin Road Kellerton NSW 2774, Tel: 02 9471 5826, Fax: 9471 5839, Dara Oyelaran, General Manager, Mobile :0438 217 564, dara.oyelaran@cushtane.com.au, Website: cushtane.com.au

```html
<!DOCTYPE html>
<html lang="en">
<head>
<meta charset="utf-8">
<title>Cushtane Business Card</title>
<link rel="stylesheet" href="https://fonts.googleapis.com/css2?family=Arimo:wght@400;700&display=swap">
<style>
  :root {
    --page-bg: #ecebe8;
    --card-white: #ffffff;
    --slate: #646567;
    --slate-dark: #5a5b5d;
    --brand-red: #b51f29;
    --ink: #58595b;
    --paper-text: #ffffff;
    --tagline-grey: #6d6e70;
    --tagline-light: #c9c9cb;
  }
  * { box-sizing: border-box; margin: 0; padding: 0; }
  html, body {
    width: 1200px; height: 848px; overflow: hidden;
    background: var(--page-bg);
    font-family: "Arimo", Arial, sans-serif;
  }
  .canvas { position: relative; width: 1200px; height: 848px; }
  .card {
    position: absolute; top: 259px;
    width: 540px; height: 330px;
    box-shadow: 0 6px 18px rgba(0,0,0,0.18);
    overflow: hidden;
  }
  .card-front { left: 40px; background: var(--card-white); }
  .card-back { left: 620px; background: var(--slate-dark); }

  .brand-panel {
    position: absolute; left: 0; top: 0; width: 270px; height: 330px;
    display: flex; flex-direction: column; justify-content: center; align-items: center;
  }
  .brand-name {
    font-weight: 700; font-size: 38px; letter-spacing: 0.5px;
    color: var(--ink); line-height: 1;
  }
  .brand-tagline {
    margin-top: 8px; font-size: 8.5px; letter-spacing: 3px;
    color: var(--tagline-grey); text-transform: uppercase; white-space: nowrap;
  }

  .identity-panel {
    position: absolute; left: 270px; top: 0; width: 270px; height: 146px;
    background: var(--slate); color: var(--paper-text);
    text-align: right; padding: 22px 20px 0 10px;
  }
  .person-name { font-size: 22px; line-height: 1.1; }
  .person-role { font-size: 11px; margin-top: 2px; }
  .address { font-size: 11px; line-height: 1.35; margin-top: 28px; }

  .contact-panel {
    position: absolute; left: 270px; top: 146px; width: 270px; height: 184px;
    background: var(--brand-red); color: var(--paper-text);
    padding: 24px 20px 0 10px;
  }
  .contact-list { list-style: none; }
  .contact-item {
    display: flex; justify-content: flex-end; align-items: center;
    font-size: 11.5px; line-height: 1; height: 20px; white-space: nowrap;
  }
  .contact-item svg { width: 11px; height: 11px; margin-left: 7px; flex: none; }

  .back-lockup {
    position: absolute; inset: 0;
    display: flex; flex-direction: column; justify-content: center; align-items: center;
  }
  .back-name {
    font-weight: 700; font-size: 58px; letter-spacing: 1px;
    color: var(--paper-text); line-height: 1;
  }
  .back-tagline {
    margin-top: 12px; font-size: 11px; letter-spacing: 4.5px;
    color: var(--tagline-light); text-transform: uppercase; white-space: nowrap;
  }
</style>
</head>
<body>
<main class="canvas">

  <section class="card card-front" aria-label="Business card front">
    <div class="brand-panel">
      <div class="brand-name">CUSHTANE</div>
      <div class="brand-tagline">Protective Packaging Solutions</div>
    </div>

    <div class="identity-panel">
      <div class="person-name">Dara Oyelaran</div>
      <div class="person-role">General Manager</div>
      <p class="address">Cushtane Pty Ltd, 14 Larkin Road<br>Kellerton NSW 2774</p>
    </div>

    <div class="contact-panel">
      <ul class="contact-list">
        <li class="contact-item">02 9471 5826
          <svg viewBox="0 0 24 24" aria-hidden="true"><path fill="#fff" d="M6.6 10.8a15.1 15.1 0 0 0 6.6 6.6l2.2-2.2c.3-.3.7-.4 1-.2 1.1.4 2.3.6 3.6.6.6 0 1 .4 1 1V20c0 .6-.4 1-1 1A17 17 0 0 1 3 4c0-.6.4-1 1-1h3.5c.6 0 1 .4 1 1 0 1.3.2 2.5.6 3.6.1.3 0 .7-.2 1z"/></svg>
        </li>
        <li class="contact-item">0438 217 564
          <svg viewBox="0 0 24 24" aria-hidden="true"><rect x="6.5" y="2" width="11" height="20" rx="2" fill="none" stroke="#fff" stroke-width="2.2"/><circle cx="12" cy="18" r="1.3" fill="#fff"/></svg>
        </li>
        <li class="contact-item">9471 5839
          <svg viewBox="0 0 24 24" aria-hidden="true"><rect x="6" y="2" width="12" height="7" fill="#fff"/><rect x="2" y="9" width="20" height="9" rx="2" fill="#fff"/><rect x="6" y="15" width="12" height="7" fill="#fff" stroke="#b51f29" stroke-width="1.5"/></svg>
        </li>
        <li class="contact-item">www.cushtane.com.au
          <svg viewBox="0 0 24 24" aria-hidden="true"><circle cx="12" cy="12" r="9.5" fill="none" stroke="#fff" stroke-width="2"/><ellipse cx="12" cy="12" rx="4" ry="9.5" fill="none" stroke="#fff" stroke-width="1.6"/><path d="M2.5 12h19" stroke="#fff" stroke-width="1.6"/></svg>
        </li>
        <li class="contact-item">dara.oyelaran@cushtane.com.au
          <svg viewBox="0 0 24 24" aria-hidden="true"><rect x="2" y="5" width="20" height="14" fill="#fff"/><path d="M2 5l10 8 10-8" fill="none" stroke="#b51f29" stroke-width="1.8"/></svg>
        </li>
      </ul>
    </div>
  </section>

  <section class="card card-back" aria-label="Business card back">
    <div class="back-lockup">
      <div class="back-name">CUSHTANE</div>
      <div class="back-tagline">Protective Packaging Solutions</div>
    </div>
  </section>

</main>
</body>
</html>
```